Development of the overall look and feel for the website. www.ReelPalsHub.com

This site is geared as a competitor to some of the major Fan websites. Where we want to be different is making a site geared more towards interaction with the Fans in the Social Media platform.
-Live streaming
-Instant Messaging
-Ability to request and purchase custom digital pieces
-Ability for Models/creators to sell blogs, podcasts, clips, screensavers, etc. through a dedicated online digital store.
-We will also have story like features similar to those found on Photoburst to allow interaction.
-Content Creators keep 85% of earnings

This should be sexy, seductive, bold, and geared towards all spectrums. From Swingers, Kink, Fetish, Milf, College, etc.

Overall the feeling should be Fun with a sense of excitement that is taboo and erotic while not scaring people away.

Trying to find the perfect blend between finding harmony/Norma Whitcombe/GBT/SoloPatron/Velvet Soiree and KRV. Monetization will be most similar to SoloPatron.

Target Market(s)

Target market should be 18+ / All Genders/ All sexuality. I want to be sure to target markets that were traditionally left out from some of the bigger platforms with all lifestyle and gender inclusion.

Industry/Entity Type

Adult Modeling, Adult Website, Streaming, Porn/fetish

Colors

Designer to choose colors to be used in the design.

Requirements
Must have
• Sex Appeal, Curiosity, Call to action, Storyboard to tell what we are about
Nice to have
• uploaded some designs that have overall look/feel.
Should not have
• Sexy but no nudity

```html
<!DOCTYPE html>
<html lang="en">
<head>
<meta charset="utf-8">
<title>ReelPalsHub – Banner Set</title>
<link rel="stylesheet" href="https://fonts.googleapis.com/css2?family=Oswald:wght@300;400;600&display=swap">
<style>
  :root {
    --canvas: #e5e7e9;
    --ink: #06060a;
    --orange: #f26122;
    --magenta: #c2188b;
    --plum: #3d0a35;
    --berry: #86166a;
    --rust: #7a2e16;
    --logo-bg: #2a0c16;
    --white: #ffffff;
  }
  * { box-sizing: border-box; margin: 0; padding: 0; }
  html, body { width: 1200px; height: 1179px; overflow: hidden; }
  body {
    position: relative;
    background: var(--canvas);
    font-family: "Oswald", sans-serif;
    color: var(--white);
  }
  .banner { position: absolute; background: var(--ink); overflow: hidden; }
  .photo { position: absolute; z-index: 0; }
  .brand-box {
    position: absolute; z-index: 1;
    background: var(--logo-bg);
    display: flex; flex-direction: column; align-items: center; justify-content: center; gap: 6px;
  }
  .brand-dot { width: 22px; height: 22px; border-radius: 50%; background: var(--white); }
  .brand-name { font-weight: 400; font-size: 15px; letter-spacing: .3px; color: var(--white); }
  .cta {
    position: absolute; z-index: 2;
    background: var(--orange);
    color: var(--white);
    font-weight: 600; font-size: 26px; letter-spacing: .3px;
    display: flex; align-items: center; justify-content: center;
    text-transform: uppercase; white-space: nowrap;
  }
  .tag { position: absolute; z-index: 2; color: var(--orange); font-weight: 400; text-transform: uppercase; line-height: 1; white-space: nowrap; }
  .bar {
    position: absolute; z-index: 2;
    font-weight: 300; font-size: 27px; text-transform: uppercase;
    display: flex; align-items: center; white-space: nowrap;
  }

  /* Leaderboard */
  .leaderboard { left: 76px; top: 62px; width: 1068px; height: 132px; }
  .leaderboard .brand-box { left: 0; top: 0; width: 129px; height: 132px; }
  .leaderboard .tag { left: 126px; font-size: 30px; }
  .leaderboard .tag.kink { top: 28px; }
  .leaderboard .tag.fetish { top: 70px; }
  .leaderboard .pitch { position: absolute; z-index: 2; left: 220px; color: var(--magenta); font-size: 33px; line-height: 1; text-transform: uppercase; white-space: nowrap; }
  .leaderboard .pitch.seekers { top: 26px; }
  .leaderboard .pitch.makers { top: 68px; }
  .leaderboard .cta { left: 456px; top: 35px; width: 266px; height: 60px; }
  .leaderboard .photo { left: 700px; top: 0; width: 368px; height: 132px;
    background: linear-gradient(90deg, var(--ink) 0%, #2b2b2f 30%, #77777c 70%, #b8b8bc 100%); }

  /* Skyscraper */
  .skyscraper { left: 78px; top: 229px; width: 235px; height: 880px; }
  .skyscraper .brand-box { left: 66px; top: 23px; width: 113px; height: 100px; }
  .skyscraper .tag.pair { left: 0; width: 100%; top: 148px; text-align: center; font-size: 31px; }
  .skyscraper .bar { left: 0; width: 100%; height: 53px; background: var(--plum); padding-left: 29px; }
  .skyscraper .bar.seekers { top: 216px; }
  .skyscraper .bar.makers { top: 279px; }
  .skyscraper .photo { left: 0; top: 332px; width: 235px; height: 474px;
    background: linear-gradient(160deg, #141216 0%, #2a2428 45%, #3a2e2e 70%, #120f12 100%); }
  .skyscraper .cta { left: 0; top: 806px; width: 235px; height: 70px; font-size: 23px; }

  /* Medium rectangle */
  .rectangle { left: 355px; top: 229px; width: 440px; height: 367px; }
  .rectangle .photo { left: 0; top: 0; width: 440px; height: 367px;
    background: linear-gradient(90deg, #4a3a33 0%, #8a6a58 30%, #5a4238 48%, #120e10 70%, var(--ink) 100%); }
  .rectangle .brand-box { left: 236px; top: 12px; width: 113px; height: 111px; }
  .rectangle .tag { left: 344px; font-size: 30px; }
  .rectangle .tag.kink { top: 28px; }
  .rectangle .tag.fetish { top: 70px; }
  .rectangle .bar { right: 0; font-weight: 400; font-size: 28px; }
  .rectangle .bar.seekers { top: 135px; width: 224px; height: 53px; background: var(--berry); padding-left: 20px; }
  .rectangle .bar.makers { top: 198px; width: 205px; height: 51px; background: var(--rust); padding-left: 10px; }
  .rectangle .cta { left: 79px; top: 285px; width: 280px; height: 59px; }
</style>
</head>
<body>

  <section class="banner leaderboard" aria-label="Leaderboard banner">
    <div class="photo" role="img" aria-label="Black and white photo of an embracing couple"></div>
    <div class="brand-box"><span class="brand-dot"></span><span class="brand-name">ReelPalsHub</span></div>
    <span class="tag kink">Kink</span>
    <span class="tag fetish">Fetish</span>
    <span class="pitch seekers">Fantasy Seekers</span>
    <span class="pitch makers">Fantasy Makers</span>
    <div class="cta">Start Your Fantasy</div>
  </section>

  <section class="banner skyscraper" aria-label="Skyscraper banner">
    <div class="brand-box"><span class="brand-dot"></span><span class="brand-name">ReelPalsHub</span></div>
    <span class="tag pair">Kink &nbsp;| &nbsp;Fetish</span>
    <div class="bar seekers">Fantasy Seekers</div>
    <div class="bar makers">Fantasy Makers</div>
    <div class="photo" role="img" aria-label="Photo of a woman in black lace held by a man in a dark suit"></div>
    <div class="cta">Start Your Fantasy</div>
  </section>

  <section class="banner rectangle" aria-label="Medium rectangle banner">
    <div class="photo" role="img" aria-label="Photo of a model in black lingerie and stockings"></div>
    <div class="brand-box"><span class="brand-dot"></span><span class="brand-name">ReelPalsHub</span></div>
    <span class="tag kink">Kink</span>
    <span class="tag fetish">Fetish</span>
    <div class="bar seekers">Fantasy Seekers</div>
    <div class="bar makers">Fantasy Makers</div>
    <div class="cta">Start Your Fantasy</div>
  </section>

</body>
</html>
```